Visitenkarten-Design für Sonnen-/Fensterschutz
Zielgruppe
KLW GmbH ist eine Firma, die Sonnenschutz und Fensterschutz anbieten.
'Ihr kompetenter Partner in Sachen Sonnenschutz- , Fenster- und Türtechnik. Sie erhalten echtes Handwerk aus dem Mühlviertel zu fairen Preisen.'
Unsere Zielgruppe sind Personen mit Haus, die am Land leben.
Firmenname: KLW GmbH
Slogan: Fenster & Sonnenschutz
Aufgabenstellung
Hier befindet sich das Logodesign: https://dx.qv/t-QwLpo7RbNs
Bitte ein schlichtes Design bereitstellen mit einer Dummy-Person:
Jonas Weidlinger + Telefonnummer + Email
Die finalen Daten bitte erst am Schluss berücksichtigen (für Gewinnerdesign)
Gerne auch hintern + vorne bedruckbar bereitstellen.

```html
<!DOCTYPE html>
<html lang="de">
<head>
<meta charset="utf-8">
<title>KLW GmbH – Visitenkarte</title>
<link href="https://fonts.googleapis.com/css2?family=Open+Sans:wght@400;600;700&display=swap" rel="stylesheet">
<style>
  :root {
    --stage: #e9e7e4;
    --paper: #ffffff;
    --paper-shade: #f1f1f1;
    --red: #e0262a;
    --red-deep: #b7221f;
    --orange: #e8622a;
    --orange-light: #ee7a45;
    --ink: #1c1c1c;
    --white: #ffffff;
  }
  * { margin: 0; padding: 0; box-sizing: border-box; }
  html, body {
    width: 1200px; height: 800px; overflow: hidden;
    background: var(--stage);
    font-family: "Open Sans", Arial, sans-serif;
  }
  .canvas {
    position: relative; width: 1200px; height: 800px;
  }
  .card {
    position: absolute; top: 255px;
    width: 510px; height: 290px;
    border-radius: 3px;
    box-shadow: 0 10px 28px rgba(0,0,0,.18);
    overflow: hidden;
  }
  /* Vorderseite */
  .card-front {
    left: 50px;
    background: linear-gradient(90deg, var(--paper-shade), var(--paper) 60%);
  }
  .front-band {
    position: absolute; top: 0; bottom: 0; left: 100px; width: 150px;
    background: linear-gradient(90deg, var(--orange) 0%, var(--red) 100%);
    display: flex; align-items: center; justify-content: center; gap: 6px;
  }
  .brand-mark {
    color: var(--white); font-weight: 700; font-size: 22px; letter-spacing: .5px;
    display: flex; align-items: center; gap: 7px;
  }
  .brand-dot {
    width: 12px; height: 12px; border-radius: 50%; background: var(--white);
  }
  .front-content {
    position: absolute; left: 285px; top: 34px; right: 24px;
  }
  .person-name {
    color: var(--red); font-weight: 700; font-size: 21px;
    padding-bottom: 4px; border-bottom: 2px solid var(--red);
    display: inline-block;
  }
  .person-role {
    color: var(--ink); font-size: 17px; margin-top: 4px;
  }
  .contact {
    margin-top: 44px; color: var(--ink); font-size: 12px; line-height: 1.55;
  }
  .company { font-weight: 700; font-size: 13px; }
  .contact-line { display: flex; align-items: center; gap: 8px; }
  .contact-line svg { width: 11px; height: 11px; flex: none; }
  .contact-web { font-weight: 700; }
  /* Rückseite */
  .card-back {
    left: 640px;
    background: linear-gradient(225deg, var(--red-deep) 0%, var(--red) 35%, var(--orange) 80%, var(--orange-light) 100%);
    display: flex; align-items: center; justify-content: center;
  }
  .back-brand { text-align: center; color: var(--white); }
  .back-brand .brand-mark { font-size: 46px; justify-content: center; gap: 14px; }
  .back-brand .brand-dot { width: 22px; height: 22px; }
  .slogan {
    margin-top: 6px; font-size: 15px; font-weight: 600;
    letter-spacing: 1.5px; text-transform: uppercase;
  }
</style>
</head>
<body>
<main class="canvas">
  <section class="card card-front" aria-label="Visitenkarte Vorderseite">
    <div class="front-band">
      <div class="brand-mark"><span class="brand-dot"></span>KLW GmbH</div>
    </div>
    <div class="front-content">
      <div class="person-name">Jonas Weidlinger</div>
      <div class="person-role">Director</div>
      <div class="contact">
        <div class="company">KLW GmbH</div>
        <div>Fenster &amp; Sonnenschutz</div>
        <div class="contact-line">
          <svg viewBox="0 0 12 12"><path fill="#e0262a" d="M2.5 1h2l1 2.5-1.3 1a6 6 0 0 0 3.3 3.3l1-1.3 2.5 1v2a1 1 0 0 1-1 1A9 9 0 0 1 1.5 2a1 1 0 0 1 1-1z"/></svg>
          0111 4820563719
        </div>
        <div class="contact-line">
          <svg viewBox="0 0 12 12"><rect x="1" y="2.5" width="10" height="7" rx="1" fill="#e0262a"/><path d="M1.5 3l4.5 3.5L10.5 3" stroke="#fff" stroke-width="1" fill="none"/></svg>
          jonas@klw-fenster.de
        </div>
        <div class="contact-line contact-web">
          <svg viewBox="0 0 12 12"><circle cx="6" cy="6" r="5" fill="#e0262a"/><g stroke="#fff" stroke-width=".8" fill="none"><ellipse cx="6" cy="6" rx="2.2" ry="5"/><path d="M1 6h10M2 3.5h8M2 8.5h8"/></g></svg>
          www.klw-fenster.de
        </div>
      </div>
    </div>
  </section>

  <section class="card card-back" aria-label="Visitenkarte Rückseite">
    <div class="back-brand">
      <div class="brand-mark"><span class="brand-dot"></span>KLW GmbH</div>
      <div class="slogan">Fenster &amp; Sonnenschutz</div>
    </div>
  </section>
</main>
</body>
</html>
```